Bramble Hounds Dog Behaviour, Training and Natural Healthcare Website

Hey there,
I need a webpage designed for my new business. It needs to be something authentic, new, fresh and representative of my business ethos. I operate out of Newcastle, NSW. I believe my job is to keep dogs alive and in their home by promoting communication and connection between dogs and their owners. This can't be achieved through training and behaviour alone. Nutritional guidance and environmental adaptation are often needed to complete the package and increase the success rate for these programs. I provide practical services such as walking coaching, nutrition profiling, behavioural modification, puppy minding, board and train programs for puppies and young dogs, training, basic and complex skills training, physical therapies and natural healthcare options. In effect taking care of the whole dog.
My motto is = Happy dogs, happy owners.
My catch cry is = promoting communication and connection between dogs and their owners.

I have in mind pages that can also link to other pages when an icon is clicked. I need a homepage, sections to explain what each of my services do (4 - which could be independent pages so I can attach photos) and a gallery. I want to have multi page function, an online capability for future retail, ability to amend and update content myself, an online booking and payment facility. My interests lie in I have seen many successes via and environmental modifications.
I've attached the logo which features prominently on my business card and Facebook page. The corporate colours are Blue with a splash of red and white. The dog being held in the healing hands must feature.

Thanks!

Target Market(s)

Australian Pet Dog Owners

Industry/Entity Type

Communication

Coding

Colors
0355a3
ec1f27
ffffff

Requirements
Must have
• The business colours (blue with a splash of red and white), the dog in the healing hands
Should not have
• Pawprints or cartoon animals

```html
<!DOCTYPE html>
<html lang="en">
<head>
<meta charset="utf-8">
<title>Bramble Hounds – Happy Dogs, Happy Owners</title>
<link href="https://fonts.googleapis.com/css2?family=Source+Sans+3:wght@300;400;600&display=swap" rel="stylesheet">
<style>
  :root{
    --blue:#0355a3;
    --blue-light:#1a8fdc;
    --blue-footer:#2a6cb9;
    --red:#ec1f27;
    --red-dark:#c0141b;
    --white:#ffffff;
    --ink:#1b1b1b;
    --dark:#1c1c1c;
    --grey:#8a8a8a;
    --social-a:#3b5998;
    --social-b:#2ea7e0;
    --social-c:#d9452f;
  }
  *{box-sizing:border-box;margin:0;padding:0}
  html,body{width:1140px;height:1200px;overflow:hidden;background:var(--white)}
  body{position:relative;font-family:"Source Sans 3",sans-serif;color:var(--ink)}
  .abs{position:absolute}

  .site-header{left:0;top:0;width:1140px;height:114px;
    background:linear-gradient(180deg,var(--blue-light) 0%,var(--blue) 100%);
    border-bottom:2px solid var(--red)}
  .brand{left:70px;top:8px;width:168px;height:100px;display:flex;flex-direction:column;align-items:center;
    background:rgba(3,70,150,.35)}
  .brand-mark{width:62px;height:62px;border-radius:50%;background:var(--white);border:3px solid var(--red);margin-top:2px}
  .brand-name{color:var(--white);font-weight:600;font-size:18px;line-height:1;margin-top:5px;letter-spacing:.3px}
  .brand-tagline{color:var(--white);font-size:8.5px;line-height:1;margin-top:3px;letter-spacing:.2px}
  .main-nav{right:113px;top:52px;display:flex;gap:26px}
  .main-nav a,.footer-nav a{color:var(--white);text-decoration:none;font-size:14px}

  .hero{left:0;top:114px;width:1140px;height:415px;
    background:
      radial-gradient(ellipse 200px 230px at 430px 230px,#e8a050 0%,#c67a33 45%,transparent 80%),
      radial-gradient(ellipse 200px 230px at 900px 230px,#eaa352 0%,#c47731 45%,transparent 80%),
      radial-gradient(ellipse 180px 120px at 440px 300px,#f0c48a 0%,transparent 70%),
      radial-gradient(ellipse 170px 120px at 920px 290px,#f3cc98 0%,transparent 70%),
      linear-gradient(90deg,#3d2e26 0%,#6e5242 18%,#8a6a52 35%,#5b463a 50%,#8a6a52 65%,#6e5242 85%,#3d2e26 100%)}
  .hero-arrow{top:166px;width:44px;height:44px}
  .hero-caption{left:0;top:365px;width:1140px;height:50px;background:rgba(40,40,40,.72);
    display:flex;align-items:center;justify-content:center;gap:24px;padding-right:30px}
  .hero-title{color:var(--white);font-size:42px;font-weight:400;line-height:1}
  .hero-tagline{color:var(--white);font-size:13px;padding-top:8px}

  .section-title{color:var(--red);font-weight:300;font-size:21px}
  .intro-title{left:79px;top:546px}
  .intro-text{left:79px;top:584px;width:734px;font-size:11.2px;line-height:14.7px;letter-spacing:-.1px}
  .btn{display:flex;align-items:center;justify-content:center;width:90px;height:36px;
    background:linear-gradient(180deg,var(--red),var(--red-dark));color:var(--white);
    font-size:14px;border-radius:2px;text-decoration:none}
  .intro-btn{left:80px;top:669px}
  .frame{border:1px solid #cfcfcf;background:var(--white);padding:5px}
  .photo{width:100%;height:100%}
  .intro-photo-frame{left:821px;top:538px;width:243px;height:171px}

  .services-title{left:80px;top:735px}
  .carousel-ctrl{left:1019px;top:740px;width:40px;height:28px;background:var(--grey)}
  .dark-band{left:0;top:895px;width:1140px;height:213px;background:linear-gradient(180deg,var(--dark),#000)}
  .service{top:776px;width:231px}
  .service .frame{height:160px;box-shadow:0 1px 3px rgba(0,0,0,.3)}
  .service-title{color:var(--red);font-weight:300;font-size:17px;margin:10px 4px 6px}
  .service-text{color:var(--white);font-size:11.8px;line-height:15px;margin:0 4px 14px}
  .service .btn{margin-left:4px}

  .site-footer{left:0;top:1108px;width:1140px;height:57px;background:var(--blue-footer)}
  .footer-nav{left:107px;top:18px;display:flex;gap:27px}
  .social{top:14px;width:29px;height:29px;border-radius:2px;box-shadow:0 1px 2px rgba(0,0,0,.3)}
  .copyright{right:119px;top:1173px;font-size:12px;color:#333}
</style>
</head>
<body>
  <header class="site-header abs">
    <div class="brand abs">
      <span class="brand-mark"></span>
      <span class="brand-name">Bramble Hounds</span>
      <span class="brand-tagline">HAPPY DOGS, HAPPY OWNERS</span>
    </div>
    <nav class="main-nav abs">
      <a href="#">Home</a><a href="#">About Us</a><a href="#">Services</a><a href="#">Blog</a><a href="#">Contact</a>
    </nav>
  </header>

  <section class="hero abs" role="img" aria-label="Two golden retrievers in a sunlit forest">
    <svg class="hero-arrow abs" style="left:77px" viewBox="0 0 44 44"><circle cx="22" cy="22" r="21" fill="none" stroke="#fff" stroke-width="1.5"/><path d="M25 13 L16 22 L25 31" fill="none" stroke="#fff" stroke-width="1.5"/></svg>
    <svg class="hero-arrow abs" style="left:1018px" viewBox="0 0 44 44"><circle cx="22" cy="22" r="21" fill="none" stroke="#fff" stroke-width="1.5"/><path d="M19 13 L28 22 L19 31" fill="none" stroke="#fff" stroke-width="1.5"/></svg>
    <div class="hero-caption abs">
      <h1 class="hero-title">Bramble Hounds</h1>
      <span class="hero-tagline">Happy Dogs, Happy Owners</span>
    </div>
  </section>

  <h2 class="section-title intro-title abs">Welcome To Our Website</h2>
  <p class="intro-text abs">Nulla facilisi. Aenean a dui vitae justo ornare luctus. Morbi ut nunc non orci facilisis tincidunt. Morbi cursus orci vel faucibus tincidunt. Sed in commodo dui, vel faucibus augue. Etiam lacinia elementum ipsum, vel molestie turpis auctor sit amet Duis magna ipsum, placerat sit amet finibus vulputate, volutpat ac ipsum. In ac libero sit amet tellus luctus sodales. Donec sodales, purus tristique aliquet rhoncus, metus augue maximus sapien, eu eleifend dolor neque mattis risus. Maecenas fermentum, orci quis porta ultricies, arcu libero fringilla risus, sed auctor enim magna nec metus. In posuere dapibus odio, eu aliquet magna sagittis molestie. Aenean placerat, ante aliquet efficitur mattis, erat nibh maximus enim</p>
  <a class="btn intro-btn abs" href="#">Read More</a>
  <div class="frame intro-photo-frame abs">
    <div class="photo" role="img" aria-label="Small terrier running on grass with a ball" style="background:radial-gradient(ellipse 40px 55px at 40% 50%,#e8e2d6 0%,transparent 80%),linear-gradient(180deg,#4a4a26 0%,#6a6a2e 30%,#86923e 65%,#5d6e2a 100%)"></div>
  </div>

  <h2 class="section-title services-title abs">We&nbsp; provide practical services</h2>
  <svg class="carousel-ctrl abs" viewBox="0 0 40 28"><path d="M14 9 L9 14 L14 19Z M26 9 L31 14 L26 19Z" fill="#fff"/><line x1="20" y1="0" x2="20" y2="28" stroke="#a3a3a3"/></svg>

  <div class="dark-band abs"></div>

  <article class="service abs" style="left:81px">
    <div class="frame"><div class="photo" role="img" aria-label="Woman walking a dog along a riverside path" style="background:linear-gradient(160deg,#dfe4e7 0%,#c3cacd 35%,#9fa6a6 55%,#b7b6ae 75%,#8a8a80 100%)"></div></div>
    <h3 class="service-title">Walking coaching</h3>
    <p class="service-text">Vivamus tincidunt erat libero, ac porta sapien consequat non. Nullam sed eros eget libero egestas mollis</p>
    <a class="btn" href="#">Read More</a>
  </article>
  <article class="service abs" style="left:331px">
    <div class="frame"><div class="photo" role="img" aria-label="Golden retriever eating from a food bowl" style="background:radial-gradient(ellipse 70px 50px at 50% 90%,#f2f2f2 0%,transparent 80%),radial-gradient(ellipse 80px 90px at 70% 35%,#c27a36 0%,transparent 80%),linear-gradient(120deg,#5fae28,#8cc640 55%,#a6c44a)"></div></div>
    <h3 class="service-title">Nutrition profiling</h3>
    <p class="service-text">Vivamus tincidunt erat libero, ac porta sapien consequat non. Nullam sed eros eget libero egestas mollis</p>
    <a class="btn" href="#">Read More</a>
  </article>
  <article class="service abs" style="left:580px">
    <div class="frame"><div class="photo" role="img" aria-label="Woman training a small white dog in a park" style="background:linear-gradient(180deg,#2f4a2a 0%,#4b6a34 40%,#7ea444 70%,#a6c85a 100%)"></div></div>
    <h3 class="service-title">Behavioural modification</h3>
    <p class="service-text">Vivamus tincidunt erat libero, ac porta sapien consequat non. Nullam sed eros eget libero egestas mollis</p>
    <a class="btn" href="#">Read More</a>
  </article>
  <article class="service abs" style="left:829px">
    <div class="frame"><div class="photo" role="img" aria-label="Golden retriever puppy lying down" style="background:radial-gradient(ellipse 80px 70px at 60% 50%,#ecd2a4 0%,transparent 80%),linear-gradient(180deg,#7a5a46 0%,#a88060 45%,#c9a47a 70%,#b07a5a 100%)"></div></div>
    <h3 class="service-title">Puppy minding</h3>
    <p class="service-text">Vivamus tincidunt erat libero, ac porta sapien consequat non. Nullam sed eros eget libero egestas mollis</p>
    <a class="btn" href="#">Read More</a>
  </article>

  <footer class="site-footer abs">
    <nav class="footer-nav abs">
      <a href="#">Home</a><a href="#">About Us</a><a href="#">Services</a><a href="#">Blog</a><a href="#">Contact</a>
    </nav>
    <span class="social abs" style="left:907px;background:var(--social-a)" aria-label="Social link"></span>
    <span class="social abs" style="left:948px;background:var(--social-b)" aria-label="Social link"></span>
    <span class="social abs" style="left:990px;background:var(--social-c)" aria-label="Social link"></span>
  </footer>
  <p class="copyright abs">© 2014.www.bramblehounds.com.au</p>
</body>
</html>
```